Building company buisness cards

We are looking for a sharp modern new look for our business cards.
We are a New Zealand based company that specialises in house and land packages.
We have attached a photo of the current logo and would like to see if it can be improved somehow if needed.
We are open to any colours but we have chosen green at this stage.
Feel free to change the font and make the logo smarter looking.
Play with the colours and see what looks best.

We want a card that looks so good know one will want to throw it away!

Target Market(s)

Home buyers

Industry/Entity Type

Building

Contact Information for Business Card

Derek Tolvane
0217394062
dtolvane@quillmarkhomesteads.co.nz
quillmarkhomesteads.co.nz

Font styles to use
Serif
Sans Serif

Colors

Designer to choose colors to be used in the design.

Requirements
Must have
• Logo and company name on one side, details on the other side
Nice to have
• Color codes for the original green are HEX #4a8028, RGB(74,128,40), CMYK(42,0,69,50)
• Round corners, Raised and/or spot UV

```html
<!DOCTYPE html>
<html lang="en">
<head>
<meta charset="utf-8">
<title>Quillmark Homesteads — Business Cards</title>
<link rel="stylesheet" href="https://fonts.googleapis.com/css2?family=Montserrat:wght@800&family=Arimo:wght@400&family=Open+Sans:wght@400&display=swap">
<style>
  :root {
    --brand-green: #4a8028;
    --card-white: #ffffff;
    --rule-grey: #8a8a8a;
    --ink: #1e1e1e;
    --backdrop: #1d1d1d;
  }
  * { margin: 0; padding: 0; box-sizing: border-box; }
  html, body {
    width: 1200px; height: 960px; overflow: hidden;
    background: var(--backdrop);
  }
  .canvas {
    position: relative; width: 1200px; height: 960px;
    display: flex; flex-direction: column; align-items: center; justify-content: center;
    gap: 60px;
  }
  .card {
    position: relative; width: 560px; height: 320px;
    border-radius: 10px; overflow: hidden;
  }

  /* Back side */
  .card--back {
    background: var(--brand-green);
    color: var(--card-white);
    text-align: center;
  }
  .card--back .wordmark {
    position: absolute; top: 108px; left: 0; right: 0;
    font-family: "Montserrat", sans-serif; font-weight: 800;
    font-size: 40px; line-height: 1; letter-spacing: -0.5px;
  }
  .card--back .wordmark-rule {
    position: absolute; top: 172px; left: 50%; width: 120px; margin-left: -60px;
    height: 1.5px; background: var(--card-white);
  }
  .card--back .web {
    position: absolute; bottom: 58px; left: 0; right: 0;
    font-family: "Open Sans", sans-serif; font-size: 15px; letter-spacing: 1.2px;
  }

  /* Front side */
  .card--front { background: var(--card-white); }
  .card--front .band { position: absolute; top: 0; left: 0; }
  .card--front .wordmark {
    position: absolute; top: 92px; left: 0; right: 0; text-align: center;
    font-family: "Montserrat", sans-serif; font-weight: 800;
    font-size: 36px; line-height: 1; letter-spacing: -0.5px;
    color: var(--brand-green);
  }
  .card--front .wordmark-rule {
    position: absolute; top: 146px; left: 50%; width: 110px; margin-left: -55px;
    height: 1.5px; background: var(--brand-green);
  }
  .card--front .person {
    position: absolute; top: 164px; left: 0; right: 0; text-align: center;
    font-family: "Arimo", sans-serif; font-size: 22px; color: var(--brand-green);
  }
  .contact {
    position: absolute; left: 150px; top: 210px;
    list-style: none;
    font-family: "Open Sans", sans-serif; font-size: 14px; color: var(--ink);
  }
  .contact li { display: flex; align-items: center; gap: 8px; height: 24px; }
  .contact li.phone { padding-left: 80px; }
  .contact svg { width: 13px; height: 13px; flex: none; }
</style>
</head>
<body>
<main class="canvas">

  <section class="card card--back" aria-label="Card back">
    <div class="wordmark">quillmark homesteads</div>
    <div class="wordmark-rule"></div>
    <div class="web">www.quillmarkhomesteads.co.nz</div>
  </section>

  <section class="card card--front" aria-label="Card front">
    <svg class="band" width="560" height="80" viewBox="0 0 560 80" aria-hidden="true">
      <path d="M0 0 H560 V56 H318 L280 26 L242 56 H0 Z" fill="var(--brand-green)"/>
      <polyline points="0,61 240,61 280,30 320,61 560,61" fill="none" stroke="var(--rule-grey)" stroke-width="2"/>
    </svg>
    <div class="wordmark">quillmark homesteads</div>
    <div class="wordmark-rule"></div>
    <div class="person">Derek Tolvane</div>
    <ul class="contact">
      <li class="phone">
        <svg viewBox="0 0 16 16" aria-hidden="true"><circle cx="8" cy="8" r="7" fill="none" stroke="var(--brand-green)" stroke-width="1.5"/><path d="M5.5 4.5 L7 4.3 L7.6 6.6 L6.8 7.3 Q7.6 9 8.9 9.4 L9.6 8.6 L11.8 9.3 L11.6 10.8 Q8 11.5 5.5 4.5 Z" fill="var(--brand-green)"/></svg>
        0217394062
      </li>
      <li class="email">
        <svg viewBox="0 0 16 16" aria-hidden="true"><rect x="1" y="3.5" width="14" height="9" rx="1" fill="var(--brand-green)"/><polyline points="1.5,4 8,9 14.5,4" fill="none" stroke="#fff" stroke-width="1.2"/></svg>
        dtolvane@quillmarkhomesteads.co.nz
      </li>
      <li class="web">
        <svg viewBox="0 0 16 16" aria-hidden="true"><circle cx="8" cy="8" r="7" fill="var(--brand-green)"/><path d="M1 8 H15 M8 1 Q4 8 8 15 M8 1 Q12 8 8 15" fill="none" stroke="#fff" stroke-width="1"/></svg>
        www.quillmarkhomesteads.co.nz
      </li>
    </ul>
  </section>

</main>
</body>
</html>
```